Stationery Design Project

We need a stationery design for our Norwegian trucking company. We have existed for about 15 years and our 12 drivers uses relatively new vehicles to transport goods around in northern Norway. Long distance routes with fresh fish og food transport is our main operations.

We have already made alogo that's printed on our trucks. The logo and a picture of our trucks is attached. I think the logo i crappy, but since its already in use, changing it is not an option in this round. Still using a better colour scheme in the overall stationery and more interesting fonts is possible (altso in the logo).

Company details:
Name: Kjelvraket AS
Organisation nr 873 615 309
Post adress: 8642 Raudvik

I like minimalism and simplicity. I am avalibly for questions in normal GMT working hours either here or on mail: ivar@fjordlast.no

Reason: Hi. Im extending the deadline because I needed some time to find a vector file of our logo. Sorry for the inconvenience

Hi, and thanks for all your interest in the project. Some updates:

-          I have decided to commit to using one of the designs. Some designer will get the payment.

-          I have extended the deadline with 24 hours since I needed some time to find our firms vector logo (a slow Swedish man was holding me up)

-          We will not choose a design before the deadline. No need to rush.

-          We have received a lot of great design and think there is a need to specified the product we want to make:

o   Business Card for all our employers. I just need the design and will duplicate with the correct numbers and name myself. The information on should be: Logo, employer’s name, Phone number, email, website, Postal number and address. Use this as a template: logo, Leif Brattvoll, 47382066, Leif@fjordlast.no,, fjordlast.no, 8642 Raudvik. The order and placement of the information is your creative decision.

o   Stickers to put on the goods we travel. On the sticker the should be the following information: Logo, phone number, Tekst and link: Fraktæ av Kjelvraket. Ke du syns? Fjordlast.no/tilbakemelding (this means: Handled by Kjelvraket. What do you think Fjordlast.no/feedback -à the link will be a feedback form). The placement the information and size is your creative decision with some stings: we have been thinking of using Drukko for printing and see that a size about 6x6 cm, 8x5 or something like that. (with 3000 copies our budget is 200 punds). Any suggestions of other suppliers are welcome. Drukko price calculator http://www.drukkolabelhouse.co.uk/digital-litho-printing/printing-labels-tags/stickers/

o   Letterhead with logo, address, phone number and organizational number.

o   Envelopes with logo,address, phone number and organizational number.

Have a nice day.

 

 

• Using the blue colour in the logo and using a similar graphic approch.

```html
<!DOCTYPE html>
<html lang="no">
<head>
<meta charset="utf-8">
<title>Kjelvraket AS – Visittkort</title>
<link rel="stylesheet" href="https://fonts.googleapis.com/css2?family=PT+Sans:wght@400;700&display=swap">
<style>
  :root {
    --backdrop: #a9a9a9;
    --paper: #ffffff;
    --navy: #0c4ea2;
    --sky: #0a75c0;
    --ink: #2a2a2a;
    --rule: #b5b5b5;
  }
  * { margin: 0; padding: 0; box-sizing: border-box; }
  html, body { width: 1200px; height: 711px; overflow: hidden; }
  body {
    position: relative;
    background: var(--backdrop);
    font-family: "PT Sans", Arial, sans-serif;
  }
  .card {
    position: absolute;
    width: 514px;
    height: 294px;
    overflow: hidden;
  }
  .card--front { left: 66px; top: 48px; background: var(--paper); border: 1px solid #8d8d8d; }
  .card--navy { left: 620px; top: 44px; background: var(--navy); }
  .card--plain { left: 66px; top: 370px; background: var(--paper); border: 1px solid #8d8d8d; }
  .card--sky { left: 620px; top: 370px; background: var(--sky); }

  .wordmark {
    position: absolute;
    left: 0; right: 0;
    display: flex;
    align-items: center;
    justify-content: center;
    gap: 14px;
    font-weight: 700;
    font-size: 46px;
    line-height: 1;
    letter-spacing: 0.5px;
  }
  .wordmark__dot {
    width: 22px; height: 22px; border-radius: 50%;
    background: currentColor;
  }
  .card--front .wordmark { top: 68px; color: var(--navy); }
  .card--navy .wordmark, .card--sky .wordmark { top: 112px; color: var(--paper); }
  .card--plain .wordmark { top: 112px; color: var(--navy); }

  .site {
    position: absolute;
    left: 0; right: 0;
    text-align: center;
    font-size: 17px;
    letter-spacing: 4px;
  }
  .card--navy .site, .card--sky .site { top: 250px; color: var(--paper); }
  .card--plain .site { top: 250px; color: var(--ink); }

  .holder {
    position: absolute;
    right: 270px;
    top: 182px;
    text-align: right;
  }
  .holder__name { font-weight: 700; font-size: 19px; color: var(--navy); line-height: 1.2; }
  .holder__org { font-size: 15px; color: var(--sky); line-height: 1.3; }

  .divider {
    position: absolute;
    left: 256px; top: 170px;
    width: 1px; height: 72px;
    background: var(--rule);
  }
  .contact {
    position: absolute;
    left: 270px; top: 176px;
    list-style: none;
    font-size: 15px;
    color: var(--ink);
    line-height: 20px;
  }
  .contact li { display: flex; align-items: center; gap: 6px; }
  .contact svg { width: 11px; height: 11px; fill: var(--sky); }

  .band {
    position: absolute;
    left: 0; bottom: 0;
    width: 514px; height: 24px;
  }
  .band__site {
    position: absolute;
    right: 46px; bottom: 3px;
    font-size: 15px;
    letter-spacing: 3.5px;
    color: var(--paper);
  }
</style>
</head>
<body>

  <section class="card card--front" aria-label="Visittkort forside">
    <div class="wordmark"><span class="wordmark__dot"></span>Kjelvraket</div>

    <div class="holder">
      <p class="holder__name">Leif Brattvoll</p>
      <p class="holder__org">Org nr 873 615 309</p>
    </div>
    <div class="divider"></div>
    <ul class="contact">
      <li><svg viewBox="0 0 12 12"><path d="M6 1 1 5v6h10V5z"/></svg>8642 Raudvik</li>
      <li><svg viewBox="0 0 12 12"><path d="M3 1c1 0 2 2 2 3S4 5 4 6s1 2 2 2 1-1 2-1 3 1 3 2-1 2-2 2C5 11 1 7 1 3c0-1 1-2 2-2z"/></svg>47382066</li>
      <li><svg viewBox="0 0 12 12"><path d="M1 3h10v7H1zM1 3l5 4 5-4" /></svg>Leif@fjordlast.no</li>
    </ul>

    <svg class="band" viewBox="0 0 514 24" aria-hidden="true">
      <rect x="0" y="13" width="250" height="11" fill="var(--sky)"/>
      <polygon points="268,24 290,0 514,0 514,24" fill="var(--navy)"/>
    </svg>
    <span class="band__site">www.fjordlast.no</span>
  </section>

  <section class="card card--navy" aria-label="Visittkort bakside, mørkeblå">
    <div class="wordmark"><span class="wordmark__dot"></span>Kjelvraket</div>
    <p class="site">www.fjordlast.no</p>
  </section>

  <section class="card card--plain" aria-label="Visittkort bakside, hvit">
    <div class="wordmark"><span class="wordmark__dot"></span>Kjelvraket</div>
    <p class="site">www.fjordlast.no</p>
  </section>

  <section class="card card--sky" aria-label="Visittkort bakside, lyseblå">
    <div class="wordmark"><span class="wordmark__dot"></span>Kjelvraket</div>
    <p class="site">www.fjordlast.no</p>
  </section>

</body>
</html>
```